wealth management firm, professional group, new model

we have a logo that works but we need a card, white background using our colors...clean look

our tag line if can be used in

Guiding Clients Toward Ownership

```html
<!DOCTYPE html>
<html lang="en">
<head>
<meta charset="utf-8">
<title>Varco Wealth Partners — Business Card</title>
<link rel="stylesheet" href="https://fonts.googleapis.com/css2?family=Lato:wght@400;700;900&display=swap">
<style>
  :root {
    --navy: #1a2e50;
    --white: #ffffff;
    --backdrop: #e9e9e9;
    --card-radius: 20px;
  }
  * { margin: 0; padding: 0; box-sizing: border-box; }
  html, body {
    width: 1200px; height: 1000px; overflow: hidden;
    background: var(--backdrop);
    font-family: "Lato", Arial, sans-serif;
  }
  .canvas { position: relative; width: 1200px; height: 1000px; }

  .card {
    position: absolute; left: 254px; width: 693px; height: 396px;
    border-radius: var(--card-radius); background: var(--white);
    overflow: hidden;
    box-shadow: 0 2px 4px rgba(0,0,0,0.18);
  }
  .card--front { top: 78px; }
  .card--back  { top: 526px; }

  .card__panel { position: absolute; inset: 0; }

  .contact {
    position: absolute; left: 54px; top: 80px; color: var(--white);
  }
  .contact__name {
    font-weight: 900; font-size: 30px; letter-spacing: 0.4px; line-height: 1;
  }
  .contact__role { font-size: 16px; margin-top: 6px; }
  .contact__list { list-style: none; margin-top: 14px; }
  .contact__item {
    display: flex; align-items: flex-start; gap: 9px;
    font-size: 15.5px; line-height: 21px; margin-bottom: 3px;
  }
  .contact__item--phone { font-size: 17.5px; }
  .contact__item svg { flex: 0 0 14px; width: 14px; height: 14px; margin-top: 3px; }
  .contact__item--address { margin-bottom: 8px; }

  .brand {
    position: absolute; text-align: center; color: var(--navy);
    font-weight: 400; line-height: 1.15; letter-spacing: 0;
  }
  .card--front .brand { left: 390px; width: 245px; top: 232px; font-size: 26px; }
  .card--back .brand { left: 0; width: 693px; top: 226px; font-size: 40px; }

  .tagline {
    position: absolute; left: 0; width: 693px; top: 340px; text-align: center;
    color: var(--navy); font-size: 17.5px;
  }
</style>
</head>
<body>
<div class="canvas">

  <section class="card card--front">
    <svg class="card__panel" viewBox="0 0 693 396" width="693" height="396" aria-hidden="true">
      <path d="M0 0 H414 Q238 200 424 396 H0 Z" fill="var(--navy)"/>
      <path d="M404 -2 Q228 200 413 398" fill="none" stroke="var(--white)" stroke-width="3"/>
    </svg>

    <div class="contact">
      <div class="contact__name">DANIEL REYES</div>
      <div class="contact__role">Founder &amp; CEO</div>
      <ul class="contact__list">
        <li class="contact__item contact__item--address">
          <svg viewBox="0 0 14 14"><path d="M7 1a4.5 4.5 0 0 0-4.5 4.5C2.5 9 7 13.5 7 13.5S11.5 9 11.5 5.5A4.5 4.5 0 0 0 7 1z" fill="currentColor"/><circle cx="7" cy="5.5" r="1.6" fill="var(--navy)"/></svg>
          <span>Street Address Here, City<br>State, Country, ZIP 123</span>
        </li>
        <li class="contact__item contact__item--phone">
          <svg viewBox="0 0 14 14"><path d="M3 1.5l2 .3.8 2.7-1.4 1.1a8 8 0 0 0 4 4l1.1-1.4 2.7.8.3 2A1.5 1.5 0 0 1 11 12.5 9.5 9.5 0 0 1 1.5 3 1.5 1.5 0 0 1 3 1.5z" fill="currentColor"/></svg>
          <span>(123) 456-7890</span>
        </li>
        <li class="contact__item contact__item--phone">
          <svg viewBox="0 0 14 14"><rect x="3.5" y="1" width="7" height="12" rx="1.2" fill="currentColor"/><rect x="4.7" y="2.6" width="4.6" height="7.4" fill="var(--navy)"/></svg>
          <span>(123) 456-7890</span>
        </li>
        <li class="contact__item contact__item--phone">
          <svg viewBox="0 0 14 14"><rect x="4" y="1.5" width="6" height="3" fill="currentColor"/><rect x="1.5" y="5" width="11" height="5" rx="1" fill="currentColor"/><rect x="4" y="8.5" width="6" height="4" fill="currentColor" stroke="var(--navy)" stroke-width="0.8"/></svg>
          <span>(123) 456-7890</span>
        </li>
        <li class="contact__item">
          <svg viewBox="0 0 14 14"><rect x="1.5" y="3" width="11" height="8" fill="currentColor"/><path d="M1.5 3.3L7 7.5l5.5-4.2" fill="none" stroke="var(--navy)" stroke-width="1"/></svg>
          <span>info@yourwebsitehere.com</span>
        </li>
        <li class="contact__item">
          <svg viewBox="0 0 14 14"><circle cx="7" cy="7" r="5.8" fill="currentColor"/><path d="M4 4.5q2 1 1.5 3t2 2M8.5 2.5q-.5 2 1.5 2.5" fill="none" stroke="var(--navy)" stroke-width="1.1"/></svg>
          <span>yourwebsitehere.com</span>
        </li>
      </ul>
    </div>

    <div class="brand">Varco Wealth Partners</div>
  </section>

  <section class="card card--back">
    <div class="brand">Varco Wealth Partners</div>
    <p class="tagline">Guiding Clients Toward Ownership</p>
  </section>

</div>
</body>
</html>
```